Letterhead and matching envelope design for a dental office

We need a new stationary design, letterhead and envelope #10, for a dental office in Denver area. We are called Bright Harbor Dental. We want a simple and minimalistic design but not a boring design. I wish to have one good point that makes it look professional. I have attached our logo. Feel free to use either one. I want the design for letterhead and envelope look like a "matching pair" but not look the same. The envelope doesn't have to be white and it will have an address window on bottom left.

Target Market(s)

everyone who visits dentist (adults)

Industry/Entity Type

Dental

Font styles to use
Other font styles liked:
• close to font on logo or something that matches well

Requirements
Must have
• professional
• simple, minimalistic
• unique point that stands out
Nice to have
• matching but not same design for letterhead and envelope
Should not have
• not look like all the other boring designs
• no flowery, distracting feats

```html
<!DOCTYPE html>
<html lang="en">
<head>
<meta charset="utf-8">
<title>Bright Harbor Dental — Letterhead</title>
<link rel="stylesheet" href="https://fonts.googleapis.com/css2?family=Arimo:wght@400;700&family=Open+Sans:wght@400;600&display=swap">
<style>
  :root {
    --backdrop: #e8e8e8;
    --paper: #ffffff;
    --brand-green: #3aaa35;
    --band-green: #bfe0ba;
    --pale-green: #eef6ec;
    --ink: #3a3a3a;
    --ink-soft: #555555;
    --rule: #e6e6e6;
  }
  * { box-sizing: border-box; margin: 0; padding: 0; }
  html, body {
    width: 1200px; height: 795px; overflow: hidden;
    background: var(--backdrop);
  }
  .letterhead {
    position: absolute; left: 338px; top: 27px;
    width: 524px; height: 741px;
    background: var(--paper);
    box-shadow: 0 2px 8px rgba(0,0,0,0.12);
    overflow: hidden;
    font-family: "Arimo", Arial, sans-serif;
    color: var(--ink);
  }
  .edge-band {
    position: absolute; right: 0; top: 0; bottom: 0; width: 12px;
    background: var(--band-green);
  }
  .top-accent {
    position: absolute; right: 0; top: 0; width: 300px; height: 4px;
    background: var(--brand-green);
  }
  .top-accent-tab {
    position: absolute; right: 0; top: 0; width: 12px; height: 52px;
    background: var(--brand-green);
  }
  .contact {
    position: absolute; right: 36px; top: 22px;
    text-align: right;
    font-family: "Open Sans", Arial, sans-serif;
    font-style: normal;
    font-size: 7.6px; line-height: 11px; color: var(--ink);
  }
  .contact .firm { color: var(--brand-green); font-weight: 600; }
  .contact .text-line { padding-right: 11px; }
  .contact .icon-line { display: flex; justify-content: flex-end; align-items: center; gap: 3px; }
  .contact svg { width: 8px; height: 8px; flex: none; }
  .brand {
    position: absolute; left: 38px; top: 96px;
    display: flex; align-items: center; gap: 8px;
    font-family: "Open Sans", Arial, sans-serif;
    font-weight: 600; font-size: 13px; letter-spacing: 1.6px;
    color: var(--brand-green); text-transform: uppercase;
  }
  .brand-dot {
    width: 14px; height: 14px; border-radius: 50%;
    background: var(--brand-green);
  }
  .header-rule {
    position: absolute; left: 38px; right: 40px; top: 176px;
    height: 1px; background: var(--rule);
  }
  .backdrop-mark {
    position: absolute; right: 30px; bottom: 110px;
    width: 230px; height: 230px; border-radius: 50%;
    background: var(--pale-green);
  }
  .letter {
    position: absolute; left: 38px; top: 228px; width: 420px;
    font-size: 9px; line-height: 12.5px; color: var(--ink-soft);
  }
  .salutation { font-weight: 700; font-size: 10.5px; color: var(--ink); margin-bottom: 10px; }
  .letter p { margin-bottom: 11px; text-align: justify; }
  .signature {
    width: 90px; height: 30px; margin-top: 22px;
    background: linear-gradient(90deg, #f1f1f1, #e4e4e4);
    border-radius: 3px;
  }
  .web {
    position: absolute; right: 18px; bottom: 46px;
    writing-mode: vertical-rl;
    transform: rotate(180deg);
    font-family: "Open Sans", Arial, sans-serif;
    font-size: 9px; letter-spacing: 1.4px; color: var(--brand-green);
    white-space: nowrap;
  }
</style>
</head>
<body>
  <main class="letterhead">
    <div class="edge-band"></div>
    <div class="top-accent"></div>
    <div class="top-accent-tab"></div>

    <address class="contact">
      <div class="firm text-line">Bright Harbor Dental</div>
      <div class="text-line">2150 Harbor Light Pkwy,</div>
      <div class="text-line">Suite 210 Westminster, CO 80031</div>
      <div class="icon-line">720-555-0148
        <svg viewBox="0 0 10 10" aria-hidden="true"><circle cx="5" cy="5" r="5" fill="#3aaa35"/><path d="M3.2 2.6l1 1-.6.7a4 4 0 0 0 2.1 2.1l.7-.6 1 1-.7.8c-2 0-4.3-2.3-4.3-4.3z" fill="#fff"/></svg>
      </div>
      <div class="icon-line">info@brightharbordental.com
        <svg viewBox="0 0 10 10" aria-hidden="true"><circle cx="5" cy="5" r="5" fill="#3aaa35"/><rect x="2.6" y="3.3" width="4.8" height="3.4" fill="none" stroke="#fff" stroke-width="0.7"/><path d="M2.6 3.3L5 5.2l2.4-1.9" fill="none" stroke="#fff" stroke-width="0.7"/></svg>
      </div>
    </address>

    <div class="brand"><span class="brand-dot"></span>Bright Harbor Dental</div>
    <div class="header-rule"></div>

    <div class="backdrop-mark" role="img" aria-label="Faint brand decoration"></div>

    <section class="letter">
      <div class="salutation">Dear Mr. Carter,</div>
      <p>Lorem ipsum dolor sit amet, consectetur adipiscing elit, sed do eiusmod tempor incididunt ut labore et dolore magna aliqua. Ut enim ad minim veniam, quis nostrud exercitation ullamco laboris nisi ut aliquip ex ea commodo consequat. Duis aute irure dolor in reprehenderit in voluptate velit esse cillum dolore.</p>
      <p>Sed ut perspiciatis unde omnis iste natus error sit voluptatem accusantium doloremque laudantium, totam rem aperiam, eaque ipsa quae ab illo inventore veritatis et quasi architecto beatae vitae dicta sunt explicabo nemo enim ipsam.</p>
      <p>Lorem ipsum dolor sit amet, consectetur adipiscing elit, sed do eiusmod tempor incididunt ut labore et dolore magna aliqua. Ut enim ad minim veniam, quis nostrud exercitation ullamco laboris nisi ut aliquip ex ea commodo consequat. Excepteur sint occaecat cupidatat non proident.</p>
      <div class="signature" role="img" aria-label="Handwritten signature"></div>
    </section>

    <div class="web">www.brightharbordental.com</div>
  </main>
</body>
</html>
```